Copperleaf Balustrade Website Redesign

I want a fresh new design for my website. Original website
www.copperleafbalustrade-example.com. Will need to add additional photos for winning designer. Please use the basic layout for new design. Looking to get a more modern, functional site to attract new customer and ne bale to highlight past projects. Need it to be easy to navigate and get in touch with me for inquiries.

Target Market(s)

Builders and home owners in WA state

Industry/Entity Type

Building, Construction, Deck building

Coding

Coded - Design and coding required

Number of Pages Required

5+ page

Font styles to use
Sans Serif

Colors
0054AA
0677BA
7BADD7
CADEEF
E8F1F8
0094D4
00A9DD
6FCCEA
C7EBF8
E9F6FB
00AB8E
00BBA5
67D7C9
C6EFE9
E9F9F6
59FF00
82FF00
B8FF75
E3FFCB
F4FFEA

Requirements
Must have
• Will need to add more photos of completed projects
Nice to have
• Fresh take on old website, something modern
Should not have
• Nothing comes to mind

```html
<!DOCTYPE html>
<html lang="en">
<head>
<meta charset="utf-8">
<title>Copperleaf Balustrade — Products</title>
<link href="https://fonts.googleapis.com/css2?family=Inter:wght@500;600;700;800&family=Jost:wght@400;500&display=swap" rel="stylesheet">
<style>
  :root {
    --green: #0e6b35;
    --green-light: #2f9c54;
    --ink: #111111;
    --body: #1f1f1f;
    --white: #ffffff;
    --footer: #1b1b1b;
    --rule: #3a3a3a;
  }
  * { margin: 0; padding: 0; box-sizing: border-box; }
  html, body { width: 775px; height: 1200px; overflow: hidden; }
  body { position: relative; background: var(--white); font-family: "Jost", sans-serif; color: var(--body); }
  .abs { position: absolute; }

  /* Header */
  .site-header { position: absolute; left: 0; top: 0; width: 775px; height: 59px; background: var(--white); }
  .brand { position: absolute; left: 36px; top: 14px; display: flex; align-items: center; gap: 7px; }
  .brand-mark { width: 18px; height: 18px; background: var(--green); }
  .brand-name { font-family: "Inter", sans-serif; font-weight: 600; font-size: 11.5px; line-height: 13px; color: var(--green); letter-spacing: 0.2px; }
  .nav { position: absolute; top: 0; height: 59px; display: flex; align-items: center; }
  .nav a { position: absolute; font-family: "Inter", sans-serif; font-weight: 500; font-size: 9px; color: var(--ink); text-decoration: none; white-space: nowrap; top: 27px; }
  .nav a.active { color: var(--green); }
  .nav-contact { position: absolute; left: 682px; top: 20px; width: 57px; height: 23px; background: var(--green); color: var(--white); font-family: "Inter", sans-serif; font-weight: 500; font-size: 9px; display: flex; align-items: center; justify-content: center; }

  /* Hero */
  .hero { position: absolute; left: 0; top: 59px; width: 775px; height: 221px; }
  .hero-photo { position: absolute; top: 0; height: 221px; }
  .hero-title { position: absolute; left: 36px; top: 150px; font-family: "Inter", sans-serif; font-weight: 800; font-size: 25px; color: var(--white); letter-spacing: 0.3px; }

  /* Featured */
  .section-title { position: absolute; left: 0; width: 775px; top: 305px; text-align: center; font-family: "Inter", sans-serif; font-weight: 700; font-size: 16px; color: var(--green); }
  .section-intro { position: absolute; left: 0; width: 775px; top: 334px; text-align: center; font-size: 8px; line-height: 13px; color: var(--body); }
  .tab { position: absolute; top: 374px; height: 22px; border: 0.6px solid var(--ink); display: flex; align-items: center; justify-content: center; font-family: "Inter", sans-serif; font-weight: 500; font-size: 8.5px; color: var(--ink); }
  .tab.active { background: var(--green); border-color: var(--green); color: var(--white); }

  .product-photo { position: absolute; width: 230px; height: 210px; }
  .product-name { position: absolute; width: 230px; font-family: "Inter", sans-serif; font-weight: 600; font-size: 10px; color: var(--green); }
  .product-desc { position: absolute; width: 230px; font-size: 8px; line-height: 13px; color: var(--body); }

  /* Footer */
  .site-footer { position: absolute; left: 0; top: 1030px; width: 775px; height: 170px; background: var(--footer); }
  .footer-brand { position: absolute; left: 38px; top: 30px; display: flex; align-items: center; gap: 9px; }
  .footer-brand .brand-mark { width: 22px; height: 22px; background: var(--green-light); }
  .footer-brand .brand-name { color: var(--green-light); font-size: 15px; line-height: 17px; font-weight: 500; }
  .footer-about { position: absolute; left: 37px; top: 81px; width: 230px; font-size: 8px; line-height: 13px; color: var(--white); }
  .footer-heading { position: absolute; top: 28px; font-family: "Inter", sans-serif; font-weight: 500; font-size: 8.5px; color: var(--green-light); }
  .footer-list { position: absolute; top: 50px; list-style: none; }
  .footer-list li { height: 19.7px; font-size: 8.5px; color: var(--white); display: flex; align-items: center; gap: 8px; }
  .footer-list li::before { content: ""; width: 4px; height: 4px; background: var(--green-light); transform: rotate(45deg); }
  .social { position: absolute; top: 50px; width: 20px; height: 20px; border-radius: 50%; background: var(--green-light); }
  .footer-rule { position: absolute; left: 0; top: 140px; width: 775px; height: 0.6px; background: var(--rule); }
  .copyright { position: absolute; left: 0; top: 148px; width: 775px; text-align: center; font-size: 8.5px; color: var(--white); }
</style>
</head>
<body>

<header class="site-header">
  <div class="brand">
    <span class="brand-mark"></span>
    <span class="brand-name">COPPERLEAF<br>BALUSTRADE</span>
  </div>
  <nav class="nav">
    <a style="left:376px">HOME</a>
    <a style="left:434px">ABOUT</a>
    <a class="active" style="left:496px">PRODUCTS</a>
    <a style="left:576px">WHY CHOOSE US</a>
  </nav>
  <div class="nav-contact">CONTACT</div>
</header>

<section class="hero">
  <div class="hero-photo" role="img" aria-label="Grey stucco house with horizontal balcony railing" style="left:0;width:140px;background:linear-gradient(180deg,#55534c,#3a3934);"></div>
  <div class="hero-photo" role="img" aria-label="Timber-framed porch with black picket railing over snowy lawn" style="left:140px;width:165px;background:linear-gradient(180deg,#8a4a24 0%,#6e6a55 45%,#b9bcbc 75%,#3b3a34 100%);"></div>
  <div class="hero-photo" role="img" aria-label="Modern home with glass balcony railings against blue sky" style="left:305px;width:165px;background:linear-gradient(180deg,#5f9ccb 0%,#7fb0d4 45%,#4a5a60 80%,#2f3430 100%);"></div>
  <div class="hero-photo" role="img" aria-label="Wooden deck with cable railing and bistro table" style="left:470px;width:166px;background:linear-gradient(180deg,#b9cde0 0%,#7f8f55 40%,#8a5c45 75%,#6e4636 100%);"></div>
  <div class="hero-photo" role="img" aria-label="Multi-level home with glass deck railings" style="left:636px;width:139px;background:linear-gradient(180deg,#d0d6dc 0%,#8c7e74 50%,#5b4e47 100%);"></div>
  <h1 class="hero-title">PRODUCTS</h1>
</section>

<h2 class="section-title">FEATURED PRODUCTS</h2>
<p class="section-intro">For a sleek, low-maintenance option, our powder-coated aluminum railings provide strength,<br>corrosion resistance, and a modern aesthetic. Available in a range of colors and finishes.</p>

<div class="tab active" style="left:169px;width:119px">ALUMINUM RAILINGS</div>
<div class="tab" style="left:294px;width:100px">GLASS RAILINGS</div>
<div class="tab" style="left:401px;width:99px">CABLE RAILINGS</div>
<div class="tab" style="left:507px;width:99px">CUSTOM DESIGN</div>

<div class="product-photo" role="img" aria-label="Covered patio with black aluminum vertical picket railing" style="left:36px;top:420px;background:linear-gradient(180deg,#6a4a36 0%,#7b6756 50%,#8c8984 80%,#9a7560 100%);"></div>
<div class="product-photo" role="img" aria-label="Apartment balconies with black vertical picket railings" style="left:272px;top:420px;background:linear-gradient(180deg,#cfd0cf 0%,#b9aa8a 45%,#a39573 80%,#355a48 100%);"></div>
<div class="product-photo" role="img" aria-label="Timber porch with picket railing overlooking snowy pines" style="left:509px;top:420px;background:linear-gradient(180deg,#a7582a 0%,#58614c 45%,#c9ced3 80%,#6d4c35 100%);"></div>

<h3 class="product-name" style="left:36px;top:645px">ALUMINUM VERTICAL PICKET</h3>
<h3 class="product-name" style="left:272px;top:645px">ALUMINUM VERTICAL PICKET</h3>
<h3 class="product-name" style="left:509px;top:645px">ALUMINUM VERTICAL PICKET</h3>
<p class="product-desc" style="left:36px;top:665px">Lorem ipsum dolor sit amet, consectetur adipiscing elit,<br>sed do eiusmod tempor</p>
<p class="product-desc" style="left:272px;top:665px">Lorem ipsum dolor sit amet, consectetur adipiscing elit,<br>sed do eiusmod tempor</p>
<p class="product-desc" style="left:509px;top:665px">Lorem ipsum dolor sit amet, consectetur adipiscing elit,<br>sed do eiusmod tempor</p>

<div class="product-photo" role="img" aria-label="Wooden deck with black horizontal aluminum railing" style="left:36px;top:725px;background:linear-gradient(180deg,#7b8a68 0%,#8c7a5a 45%,#9a7350 100%);"></div>
<div class="product-photo" role="img" aria-label="Grey stucco home with horizontal balcony railing" style="left:272px;top:725px;background:linear-gradient(180deg,#5c5a54 0%,#4d4c47 55%,#3a3a37 100%);"></div>
<div class="product-photo" role="img" aria-label="Exterior stairs with horizontal aluminum handrail" style="left:509px;top:725px;background:linear-gradient(180deg,#b5b8b9 0%,#66645e 45%,#5a5852 80%,#7d7768 100%);"></div>

<h3 class="product-name" style="left:36px;top:950px">ALUMINUM HORIZONTAL RAILING</h3>
<h3 class="product-name" style="left:272px;top:950px">ALUMINUM HORIZONTAL RAILING</h3>
<h3 class="product-name" style="left:509px;top:950px">ALUMINUM HORIZONTAL RAILING</h3>
<p class="product-desc" style="left:36px;top:970px">Lorem ipsum dolor sit amet, consectetur adipiscing elit,<br>sed do eiusmod tempor</p>
<p class="product-desc" style="left:272px;top:970px">Lorem ipsum dolor sit amet, consectetur adipiscing elit,<br>sed do eiusmod tempor</p>
<p class="product-desc" style="left:509px;top:970px">Lorem ipsum dolor sit amet, consectetur adipiscing elit,<br>sed do eiusmod tempor</p>

<footer class="site-footer">
  <div class="footer-brand">
    <span class="brand-mark"></span>
    <span class="brand-name">COPPERLEAF<br>BALUSTRADE</span>
  </div>
  <p class="footer-about">we specialize in crafting custom railing systems designed to withstand the region’s unique climate while enhancing the beauty of your outdoor living spaces.</p>

  <h4 class="footer-heading" style="left:326px">QUICK LINKS</h4>
  <ul class="footer-list" style="left:328px">
    <li>Home</li><li>Product</li><li>Why Choose us</li><li>Contact</li>
  </ul>

  <h4 class="footer-heading" style="left:469px">OUR PRODUCT</h4>
  <ul class="footer-list" style="left:470px">
    <li>Aluminum Railings</li><li>Glass Railings</li><li>Cable Railings</li><li>Custom design</li>
  </ul>

  <h4 class="footer-heading" style="left:637px;top:27px">CONNECT WITH US</h4>
  <span class="social" style="left:636px" aria-label="Social link"></span>
  <span class="social" style="left:661px" aria-label="Social link"></span>
  <span class="social" style="left:687px" aria-label="Social link"></span>
  <span class="social" style="left:714px" aria-label="Social link"></span>

  <div class="footer-rule"></div>
  <p class="copyright">© Copyright 2024&nbsp; All Rights Reserved</p>
</footer>

</body>
</html>
```